Bright and beautiful business card for a coach

I'm a personal and business coach based in Perth, Australia. I need a business card that whilst subtle and elegant, will stand out and appeal on a table full of cards.

My business name is Fern Mentoring and the business card must represent the warmth and brightness implied in the name, without being gimmicky. It must have a warmth and appeal and be easy to read.

I prefer clean, minimalist designs.

It must align with the feel of my website and socials: https://www.fernmentoring-example.com.au/
https://www.instagram.com/fernmentoringau/
https://www.facebook.com/fernmentoringau
Updates

Hi Designers Thank you so much for taking the time to submit designs. I wonder if I could have explained myself a little better. Most of the designs that have been submitted look rather formal and many have quite corporate looking embellishments on them (to my eye). I would like softer, warmer, more organic. I’m open to people playing about and being more abstract, using softer embellishments (e.g the line drawing flowers and grasses I’ve used in my socials) incorporating other colours from my palette or like the social icons in my email signature (in PDF), perhaps playing with size/oversize, playing with the bleed. Please don’t be constrained by what I’ve already done, it merely needs to compliment. I’m sorry if I’m not using the right words or have led you astray. I’m no designer, but I’ve done my website, socials, email signature etc all myself (my logo was a design contest) and I was really hoping for my business card to be something more creative than I could have made with a template. Reminder: No black cards/sides please. Thank you 😊

Target Market(s)

Individuals, most likely but not all female. Creative thinkers. Likely professionals.

Industry/Entity Type

Business & Personal Coach

Contact Information for Business Card

(Fern Mentoring Logo) Name: Greta Pellham; Title: Business & Personal Coach; Phone number: +61 (0)458 913307; Email: greta@fernmentoring-example.com.au; Website: https://fernmentoring-example.com.au; Social icons for Facebook, Instagram & LinkedIn: @fernmentoringAU. Optional strapline: "A thinking partner to help you cut through the noise"

Font styles to use
Sans Serif

Colors
00AB8E
00BBA5
67D7C9
C6EFE9
E9F9F6
59FF00
82FF00
B8FF75
E3FFCB
F4FFEA
FFC000
F8CF3A
FAE287
FDF2CF
FEFAEE

Requirements
Must have
• Must align with feel of my website and socials. Must have a pop of #FFC000 (possibly whole of one side, or at least a block). Bright or white background. Easy to read.
Nice to have
• Possibly incorporate the sunshine/grass picture I have used in website and socials - will upload.
Should not have
• Must not be black or dark. Not impersonal or corporate looking.

```html
<!DOCTYPE html>
<html lang="en">
<head>
<meta charset="utf-8">
<title>Fern Mentoring – Business Card</title>
<link rel="stylesheet" href="https://fonts.googleapis.com/css2?family=Montserrat:wght@700;800&family=Roboto:wght@400;500&display=swap">
<style>
  :root {
    --canvas: #ecebe7;
    --white: #ffffff;
    --amber-deep: #b8611f;
    --amber-mid: #d98a25;
    --amber-bright: #f5c322;
    --pill-grey: #8e8e8e;
    --logo-ink: #c8781f;
    --green-flat: #5e8f34;
    --green-soft: #6f9d3f;
    --shadow: rgba(0, 0, 0, 0.18);
  }
  * { box-sizing: border-box; margin: 0; padding: 0; }
  html, body {
    width: 1200px; height: 900px; overflow: hidden;
    background: var(--canvas);
    font-family: "Roboto", Arial, sans-serif;
  }
  .stage { position: relative; width: 1200px; height: 900px; }
  .card {
    position: absolute; width: 640px; height: 366px;
    border-radius: 22px; overflow: hidden;
    box-shadow: 0 14px 30px var(--shadow);
  }

  /* Front side */
  .card--front { left: 470px; top: 56px; }
  .front-photo {
    position: absolute; inset: 0;
    background: linear-gradient(180deg, var(--green-soft) 0%, var(--green-flat) 100%);
  }
  .front-brand {
    position: absolute; left: 60px; top: 150px;
    display: flex; align-items: center; gap: 14px;
    color: var(--white);
    font-family: "Roboto", Arial, sans-serif; font-weight: 400;
    font-size: 46px; letter-spacing: 1px;
  }
  .brand-dot {
    width: 22px; height: 22px; border-radius: 50%;
    border: 2px solid currentColor;
  }

  /* Back side */
  .card--back { left: 130px; top: 470px; background: var(--white); }
  .back-band {
    position: absolute; left: 0; right: 0; top: 190px; bottom: 0;
    background: linear-gradient(100deg, var(--amber-deep) 0%, var(--amber-mid) 45%, var(--amber-bright) 100%);
  }
  .back-brand {
    position: absolute; left: 0; right: 0; top: 70px;
    display: flex; justify-content: center; align-items: center; gap: 14px;
    color: var(--logo-ink);
    font-weight: 400; font-size: 44px; letter-spacing: 1px;
  }
  .strapline {
    position: absolute; left: 110px; top: 172px;
    padding: 7px 26px;
    background: var(--pill-grey); color: var(--white);
    border: 3px solid var(--white);
    border-radius: 22px;
    font-size: 17px; white-space: nowrap;
  }
  .person {
    position: absolute; left: 36px; top: 250px; color: var(--white);
  }
  .person-name {
    font-family: "Montserrat", Arial, sans-serif; font-weight: 800;
    font-size: 27px; letter-spacing: 1px; line-height: 1.1;
  }
  .person-title { font-size: 17px; margin-top: 4px; }
  .divider {
    position: absolute; left: 300px; top: 236px;
    width: 2px; height: 106px; background: var(--white);
  }
  .contacts {
    position: absolute; left: 318px; top: 234px;
    list-style: none; color: var(--white); font-size: 15px;
  }
  .contacts li {
    display: flex; align-items: center; gap: 8px; height: 27px; white-space: nowrap;
  }
  .contact-icon { width: 15px; height: 15px; flex: none; fill: var(--white); }
  .social-dot {
    width: 15px; height: 15px; border-radius: 50%;
    background: var(--white); flex: none;
  }
</style>
</head>
<body>
<main class="stage">

  <section class="card card--front">
    <div class="front-photo" role="img" aria-label="Photo area: sunlit close-up of green grass"></div>
    <div class="front-brand"><span class="brand-dot"></span>Fern Mentoring</div>
  </section>

  <section class="card card--back">
    <div class="back-band"></div>
    <div class="back-brand"><span class="brand-dot"></span>Fern Mentoring</div>
    <p class="strapline">A thinking partner to help you cut through the noise</p>

    <div class="person">
      <h1 class="person-name">GRETA PELLHAM</h1>
      <p class="person-title">Business &amp; Personal Coach</p>
    </div>

    <div class="divider"></div>

    <ul class="contacts">
      <li>
        <svg class="contact-icon" viewBox="0 0 16 16" aria-hidden="true"><path d="M3 1h3l1.5 4-2 1.2a9 9 0 0 0 4.3 4.3L11 8.5l4 1.5v3a2 2 0 0 1-2 2A12 12 0 0 1 1 3a2 2 0 0 1 2-2z"/></svg>
        +61 (0)458 913307
      </li>
      <li>
        <svg class="contact-icon" viewBox="0 0 16 16" aria-hidden="true"><path d="M1 3h14v10H1z M2.5 4.5 8 9l5.5-4.5" fill="none" stroke="#fff" stroke-width="1.5"/></svg>
        greta@fernmentoring-example.com.au
      </li>
      <li>
        <svg class="contact-icon" viewBox="0 0 16 16" aria-hidden="true"><g fill="none" stroke="#fff" stroke-width="1.4"><circle cx="8" cy="8" r="6.5"/><ellipse cx="8" cy="8" rx="3" ry="6.5"/><path d="M1.5 8h13"/></g></svg>
        www.fernmentoring-example.com.au
      </li>
      <li>
        <span class="social-dot"></span>
        @fernmentoringAU
      </li>
    </ul>
  </section>

</main>
</body>
</html>
```